Letterhead, stationery and email signature for construction business

I need the letterhead, stationery and email signature designs for a construction business. I want them to have a corporate feel to them.

I've attached the logo for reference.

```html
<!DOCTYPE html>
<html lang="en">
<head>
<meta charset="utf-8">
<title>Harlow Build Letterhead</title>
<link href="https://fonts.googleapis.com/css2?family=Lato:wght@400;700;900&family=Open+Sans:wght@400&family=Parisienne&display=swap" rel="stylesheet">
<style>
  :root {
    --brand-blue: #2f55a4;
    --accent-grey: #6e7590;
    --ink: #1c1c1c;
    --paper: #ffffff;
    --backdrop: #e3e3e3;
  }
  * { margin: 0; padding: 0; box-sizing: border-box; }
  html, body { width: 1200px; height: 1141px; overflow: hidden; background: var(--backdrop); }
  .letterhead {
    position: absolute; left: 210px; top: 19px;
    width: 780px; height: 1103px;
    background: var(--paper);
    box-shadow: 0 4px 14px rgba(0,0,0,0.18);
    overflow: hidden;
    font-family: "Lato", sans-serif;
    color: var(--ink);
  }
  .brand {
    position: absolute; left: 39px; top: 78px;
    display: flex; align-items: center; gap: 14px;
  }
  .brand-square { width: 42px; height: 42px; background: var(--brand-blue); }
  .brand-name {
    font-family: "Lato", sans-serif; font-weight: 900;
    font-size: 40px; letter-spacing: 1px; color: var(--brand-blue);
    line-height: 1;
  }
  .header-divider {
    position: absolute; left: 512px; top: 45px;
    width: 2px; height: 112px; background: var(--brand-blue);
  }
  .contact {
    position: absolute; left: 540px; top: 40px;
    font-family: "Open Sans", sans-serif; font-style: normal;
    font-size: 17px; line-height: 22.5px; color: var(--ink);
  }
  .contact-address { margin-bottom: 7px; }
  .contact-line { display: flex; align-items: center; gap: 6px; }
  .contact-line svg { width: 13px; height: 13px; flex: none; }
  .header-rule {
    position: absolute; left: 39px; top: 195px;
    width: 703px; height: 2px; background: var(--brand-blue);
  }
  .letter-body {
    position: absolute; left: 39px; top: 253px; width: 703px;
    font-size: 15.5px; line-height: 18.5px;
  }
  .letter-date { margin-bottom: 19px; }
  .recipient { margin-bottom: 17px; }
  .salutation { font-size: 19px; font-weight: 700; margin: 12px 0 24px; }
  .paragraph {
    font-size: 15.6px; line-height: 17px; text-align: justify;
    margin-bottom: 17px;
  }
  .closing { margin-top: 36px; }
  .signature {
    position: absolute; left: 39px; top: 880px;
    font-family: "Parisienne", cursive; font-size: 34px; color: #111;
  }
  .footer-rule {
    position: absolute; left: 0; bottom: 70px;
    width: 780px; height: 4px; background: var(--accent-grey);
  }
  .footer-band {
    position: absolute; left: 0; bottom: 0;
    width: 780px; height: 62px; background: var(--brand-blue);
  }
</style>
</head>
<body>
  <article class="letterhead">
    <header>
      <div class="brand">
        <span class="brand-square"></span>
        <span class="brand-name">HARLOW BUILD</span>
      </div>
      <div class="header-divider"></div>
      <address class="contact">
        <div class="contact-address">Your address, City<br>State, Zip 1234</div>
        <div class="contact-line">
          <svg viewBox="0 0 14 14" aria-hidden="true"><path fill="#2f55a4" d="M1 5c0-2 3-3 6-3s6 1 6 3v1h-3V5H4v1H1zM3 7h8l1 5H2z"/></svg>
          123 456 789
        </div>
        <div class="contact-line">
          <svg viewBox="0 0 14 14" aria-hidden="true"><rect x="1" y="3" width="12" height="8" fill="#2f55a4"/><path d="M1 3l6 5 6-5" stroke="#fff" stroke-width="1.2" fill="none"/></svg>
          info@yourmail.com
        </div>
        <div class="contact-line">
          <svg viewBox="0 0 14 14" aria-hidden="true"><circle cx="7" cy="7" r="6" fill="#2f55a4"/><path d="M1 7h12M7 1c-3 3-3 9 0 12M7 1c3 3 3 9 0 12" stroke="#fff" stroke-width="0.9" fill="none"/></svg>
          www.yourwebsite.com
        </div>
      </address>
      <div class="header-rule"></div>
    </header>

    <section class="letter-body">
      <p class="letter-date">January-03-2020</p>
      <p class="recipient">Mr, Peter Lane<br>President</p>
      <p class="recipient">Northway Corporation<br>123 Street Name, Suite# 10<br>City, State, 120023</p>
      <h2 class="salutation">Dear Mr, Peter</h2>
      <p class="paragraph">Lorem ipsum dolor sit amet, consectetur adipiscing elit, sed do eiusmod tempor incididunt ut labore et dolore magna aliqua. Ut enim ad minim veniam, quis nostrud exercitation ullamco laboris nisi ut aliquip ex ea commodo consequat. Duis aute irure dolor in reprehenderit in voluptate velit esse cillum dolore eu fugiat nulla pariatur.</p>
      <p class="paragraph">Lorem ipsum dolor sit amet, consectetur adipiscing elit, sed do eiusmod tempor incididunt ut labore et dolore magna aliqua. Ut enim ad minim veniam, quis nostrud exercitation ullamco laboris nisi ut aliquip ex ea commodo consequat. Duis aute irure dolor in reprehenderit in voluptate velit esse cillum dolore eu fugiat nulla pariatur.</p>
      <p class="paragraph">Lorem ipsum dolor sit amet, consectetur adipiscing elit, sed do eiusmod tempor incididunt ut labore et dolore magna aliqua. Ut enim ad minim veniam, quis nostrud exercitation ullamco laboris nisi ut aliquip ex ea commodo consequat.</p>
      <p class="paragraph">Excepteur sint occaecat cupidatat non proident, sunt in culpa qui officia deserunt mollit anim id est laborum. re et dolore magnam aliquam quaerat voluptatem.</p>
      <p class="closing">Regards</p>
    </section>

    <p class="signature">Daniel Hart</p>

    <footer>
      <div class="footer-rule"></div>
      <div class="footer-band"></div>
    </footer>
  </article>
</body>
</html>
```